Expedition Cruise Sales Website for the Polar Regions (Antarctica & Arctic)

This will be a website for selling cruises.
This site should have a homepage, a ship page, destinations, and itineraries.
I have created a file specifying each page, and it is attached.
Pages:
1. Home
2. Cruise Lines
- 2.1 Ships
3. Destinations
- 3.1 Region - 3.2 Country - 3.3 City
4. Itineraries
- 4.1 Itinerary
5. Blog / Travel Tips 6. About Us
7. Contact
Please take a look on the attached pdf
Target Market(s)
Expedition Travelers
Coding
Coded - Design and coding required
Number of Pages Required
5+ page
Font styles to use
Look and feel
Each slider illustrates characteristics of the customer's brand and the style your logo design should communicate.

```html
<!DOCTYPE html>
<html lang="en">
<head>
<meta charset="utf-8">
<title>Glacierra — Expedition Cruises</title>
<link href="https://fonts.googleapis.com/css2?family=Poppins:wght@300;400;500;600;700&display=swap" rel="stylesheet">
<style>
:root{
  --blue:#2f6fbf;
  --blue-dark:#2a62a8;
  --ink:#161a20;
  --muted:#6a6f78;
  --line:#e3e6ea;
  --bg:#ffffff;
  --night:#1f2e3c;
  --foot:#2f6db3;
}
*{box-sizing:border-box;margin:0;padding:0}
html,body{width:1200px;height:5021px;overflow:hidden;background:var(--bg)}
body{font-family:"Poppins",sans-serif;color:var(--ink);position:relative}
.abs{position:absolute}
.accent{color:var(--blue)}
.ph{position:absolute;border-radius:12px}
.btn{position:absolute;background:var(--blue);color:#fff;font-weight:600;font-size:12px;border-radius:20px;display:flex;align-items:center;justify-content:center}
.center{text-align:center;left:0;width:1200px}
.h2{font-size:34px;font-weight:500}
.lead{font-size:13px;color:var(--muted);line-height:20px;font-weight:300}
/* nav */
.nav-brand{left:30px;top:22px;display:flex;align-items:center;gap:8px;font-weight:600;font-size:20px;color:var(--blue)}
.nav-brand i{width:14px;height:14px;border-radius:50%;background:var(--blue);display:block}
.nav-links{left:400px;top:30px;display:flex;gap:16px;font-size:13px;color:var(--muted)}
.nav-links b{color:var(--ink);font-weight:600}
/* booking */
.booking{left:832px;top:185px;width:308px;height:263px;background:#fff;border-radius:10px;padding:26px 20px}
.booking h3{font-size:20px;font-weight:500;line-height:30px}
.field{height:34px;border:1px solid var(--line);background:#f6f7f9;border-radius:17px;margin-top:14px;font-size:12px;color:#a4a9b0;display:flex;align-items:center;justify-content:space-between;padding:0 14px}
/* cruise cards */
.cruise{position:absolute;top:818px;width:353px}
.cruise .ph{position:relative;height:244px;display:block}
.cruise h4{color:var(--blue);font-size:19px;font-weight:600;margin-top:20px}
.cruise p{font-size:13px;color:var(--muted);line-height:20px;font-weight:300;margin-top:2px}
.cruise .more{display:flex;align-items:center;gap:18px;font-weight:600;font-size:15px;margin-top:16px}
/* pills */
.pill{position:absolute;height:26px;border-radius:13px;font-size:12px;display:flex;align-items:center;justify-content:center;gap:6px;border:1px solid #d4dce8;color:#9aa3b0}
.pill.on{background:#e9f0fa;border-color:var(--blue);color:var(--blue)}
.pill.on::before{content:"";width:6px;height:6px;border-radius:50%;background:var(--blue)}
.arrow{position:absolute;width:36px;height:36px;border-radius:50%;background:#fff;top:1620px;display:flex;align-items:center;justify-content:center;box-shadow:0 2px 8px rgba(0,0,0,.1)}
/* blog */
.post{position:absolute;top:2570px;width:275px;height:378px;border:1px solid var(--line);border-radius:12px;padding:12px}
.post .ph{position:relative;display:block;height:191px;border-radius:6px}
.post .go{position:absolute;right:22px;top:22px;width:40px;height:40px;border-radius:50%;background:#fff;display:flex;align-items:center;justify-content:center}
.post time{display:block;font-size:11px;color:var(--muted);margin-top:16px}
.post h4{font-size:17px;font-weight:600;line-height:28px;margin-top:6px}
.post p{font-size:11.5px;color:var(--muted);line-height:19px;font-weight:300;margin-top:8px}
/* testimonials */
.quote{position:absolute;top:4120px;width:357px;height:211px;border:2px solid #d8dbe0;border-radius:12px;background:#f4f5f7;padding:18px 26px}
.quote .who{display:flex;align-items:center;gap:10px}
.quote .av{width:38px;height:38px;border-radius:50%;background:#8c949e}
.quote .who b{font-size:11px;font-weight:600;display:block}
.quote .who span{font-size:10px;color:var(--muted)}
.quote .stars{margin-left:auto}
.quote p{font-size:12px;color:var(--muted);text-align:center;line-height:20px;padding:28px 46px 0;font-weight:300}
.qm{position:absolute;font-size:64px;color:#c5c9cf;font-family:Georgia,serif;line-height:1}
/* footer */
.foot-col{position:absolute;top:4790px;font-size:17px;color:#fff;line-height:32px;font-weight:300}
.foot-col h5{font-size:17px;font-weight:600}
</style>
</head>
<body>

<svg width="0" height="0" style="position:absolute">
  <defs>
    <symbol id="star" viewBox="0 0 20 20"><path d="M10 1l2.7 5.9 6.3.7-4.7 4.3 1.3 6.3L10 15l-5.6 3.2 1.3-6.3L1 7.6l6.3-.7z" fill="#f5c31c"/></symbol>
    <symbol id="arr" viewBox="0 0 30 12"><path d="M0 6h28M22 1l6 5-6 5" stroke="#2f6fbf" stroke-width="1.6" fill="none"/></symbol>
  </defs>
</svg>

<!-- Header -->
<header>
  <div class="abs nav-brand"><i></i>Glacierra</div>
  <nav class="abs nav-links"><b>Home</b><span>Cruise Lines</span><span>Destinations</span><span>Itineraries</span><span>Contact</span></nav>
  <div class="btn" style="left:990px;top:23px;width:172px;height:36px">Get Started now</div>
</header>

<!-- Hero -->
<section class="hero">
  <div class="ph" role="img" aria-label="Aerial view of cruise ships docked in turquoise water" style="left:27px;top:107px;width:1135px;height:507px;border-radius:18px;background:linear-gradient(120deg,#1f8fc4,#36b6d6 45%,#1a6f9e 80%,#2a9cc0)"></div>
  <div class="abs booking">
    <h3>Book your <span class="accent">sailing<br>now</span></h3>
    <div class="field">Choose a date
      <svg width="12" height="12" viewBox="0 0 12 12"><rect x="1" y="2" width="10" height="9" rx="1" fill="none" stroke="#555"/><path d="M1 5h10M4 1v2M8 1v2" stroke="#555"/></svg></div>
    <div class="field">Select Passanger
      <svg width="10" height="8" viewBox="0 0 10 8"><path d="M1 1h8L5 7z" fill="#444"/></svg></div>
    <div class="btn" style="position:relative;margin-top:48px;height:36px;gap:10px">
      <svg width="12" height="12" viewBox="0 0 12 12"><circle cx="5" cy="5" r="3.8" stroke="#fff" stroke-width="1.6" fill="none"/><path d="M8 8l3 3" stroke="#fff" stroke-width="1.6"/></svg>Check Available</div>
  </div>
</section>

<!-- Cruise line -->
<section>
  <h2 class="abs center h2" style="top:654px"><span class="accent">Cruise</span> Line</h2>
  <p class="abs lead" style="top:710px;left:320px;width:560px;text-align:center">Experience the breathtaking charm of a captivating beach destination, where the blue sky meets the gentle crashing waves. Every corner offers extraordinary natural beauty, from the soft white sands to the vibrant coral reefs.</p>

  <article class="cruise" style="left:45px">
    <div class="ph" role="img" aria-label="Rocky sea stacks beside a sandy coast" style="background:linear-gradient(#9fc6e6,#8a8478 55%,#c9b79a)"></div>
    <h4>Coastal Adventure</h4>
    <p>Experience the beauty of the coastline as you sail along the stunning shore.</p>
    <div class="more">Explore now <svg width="30" height="12"><use href="#arr"/></svg></div>
  </article>
  <article class="cruise" style="left:423px">
    <div class="ph" role="img" aria-label="Tall sailing ship anchored near green hills" style="background:linear-gradient(#b9d3ea,#6f7a6a 55%,#8b6a4f)"></div>
    <h4>Island Exploration Tour</h4>
    <p>Visit stunning islands and discover their unique culture and landscapes</p>
    <div class="more">Explore now <svg width="30" height="12"><use href="#arr"/></svg></div>
  </article>
  <article class="cruise" style="left:801px">
    <div class="ph" role="img" aria-label="White river cruise boat on blue water" style="background:linear-gradient(135deg,#2f78b0,#4a9bd0 50%,#2b6f9e)"></div>
    <h4>Beautiful River Cruise</h4>
    <p>Glide through beautiful rivers, surrounded by the tranquility of nature</p>
    <div class="more">Explore now <svg width="30" height="12"><use href="#arr"/></svg></div>
  </article>
</section>

<!-- Destinations -->
<section>
  <p class="abs" style="left:64px;top:1262px;font-size:12px">Destination</p>
  <h2 class="abs h2" style="left:64px;top:1280px;line-height:50px">Escape to Our<br><span class="accent">Favorite Destination</span></h2>
  <div class="pill on" style="left:780px;top:1277px;width:93px">Region</div>
  <div class="pill" style="left:880px;top:1277px;width:98px">Country</div>
  <div class="pill" style="left:985px;top:1277px;width:68px">City</div>
  <p class="abs lead" style="left:780px;top:1330px;width:380px;font-size:12.5px">Explore our stunning beach destinations, each offering unique experiences. Discover the serene shores of Coral Bay, where you can relax on powdery white sands.</p>

  <div class="ph" role="img" aria-label="Palm tree on a bright beach" style="left:23px;top:1530px;width:180px;height:215px;background:linear-gradient(#8fc3de,#cfe3ea 60%,#e8ddc7);opacity:.8"></div>
  <div class="ph" role="img" aria-label="Misty lake with hills" style="left:230px;top:1501px;width:226px;height:273px;background:linear-gradient(#c9d3d8,#7f9199 55%,#5e4a3a)"></div>
  <div class="ph" role="img" aria-label="Coastal peak above a blue bay" style="left:483px;top:1476px;width:232px;height:325px;background:linear-gradient(#86a7c2,#5c7b86 30%,#2f79b0 60%,#5aa6d4)"></div>
  <div class="ph" role="img" aria-label="Dark rocky coastline seen from above" style="left:744px;top:1501px;width:224px;height:273px;background:linear-gradient(135deg,#3d4a4e,#1e4e6e 55%,#2f3a3d)"></div>
  <div class="ph" role="img" aria-label="Sunset over the sea" style="left:996px;top:1530px;width:181px;height:215px;background:linear-gradient(#e5a85a,#c96b3a 45%,#2d4a6a);opacity:.85"></div>
  <div class="arrow" style="left:40px"><svg width="14" height="12" viewBox="0 0 14 12"><path d="M13 6H2M6 1L1 6l5 5" stroke="#2f6fbf" stroke-width="1.6" fill="none"/></svg></div>
  <div class="arrow" style="left:1124px"><svg width="14" height="12" viewBox="0 0 14 12"><path d="M1 6h11M8 1l5 5-5 5" stroke="#2f6fbf" stroke-width="1.6" fill="none"/></svg></div>
  <h4 class="abs center" style="top:1826px;font-size:20px;font-weight:500">Chapmans peak</h4>
  <p class="abs center" style="top:1858px;font-size:15px;color:var(--muted);display:flex;justify-content:center;gap:22px;align-items:center">
    <svg width="20" height="22" viewBox="0 0 20 22"><path d="M10 1a6 6 0 0 0-6 6c0 4.5 6 10 6 10s6-5.5 6-10a6 6 0 0 0-6-6z" fill="none" stroke="#444" stroke-width="1.5"/><circle cx="10" cy="7" r="2" fill="#444"/><ellipse cx="10" cy="19.5" rx="7" ry="1.8" fill="none" stroke="#444" stroke-width="1.2"/></svg>south africa</p>
</section>

<!-- Itineraries -->
<section>
  <div class="ph" role="img" aria-label="Traveler standing on a stone wall overlooking a coastal mountain" style="left:64px;top:1963px;width:563px;height:394px;background:linear-gradient(#7fb3de,#4b87b4 40%,#2c9bb7 60%,#a68d6a 85%)"></div>
  <p class="abs" style="left:672px;top:1964px;font-size:12px">Itineraries</p>
  <h2 class="abs h2" style="left:672px;top:1984px">Achieve Your <span class="accent">Journey</span></h2>
  <p class="abs lead" style="left:672px;top:2044px;width:500px;font-size:12.5px">Embark on an unforgettable journey to a breathtaking coastal paradise, where the vibrant azure skies meet the gentle whispers of the ocean waves. As you explore this idyllic destination, you'll be captivated by the stunning landscapes that unfold before you. Picture yourself strolling along powdery white beaches that stretch for miles, their soft sands inviting you to relax and unwind. Dive into the crystal-clear waters to discover vibrant coral gardens teeming with colorful marine life, each moment revealing the wonders of the underwater world</p>
  <div class="btn" style="left:672px;top:2246px;width:135px;height:36px">Get Started now</div>
</section>

<!-- Blog -->
<section>
  <h2 class="abs center h2" style="top:2397px">Blog <span class="accent">And Tips</span></h2>
  <p class="abs lead" style="top:2450px;left:320px;width:560px;text-align:center">Discover the hidden gems of our stunning beach paradise! From serene shores to lively coral gardens, each spot is a treasure waiting to be explored. Dive into our tips for the best local eateries, thrilling water sports, and must-see attractions that will make your beach getaway unforgettable.</p>

  <article class="post" style="left:21px">
    <div class="ph" role="img" aria-label="Canal lined with old buildings and boats" style="background:linear-gradient(#9cc2df,#8a6d55 50%,#2f6e6a)"></div>
    <div class="go"><svg width="12" height="12"><path d="M2 10L10 2M4 2h6v6" stroke="#2f6fbf" stroke-width="1.6" fill="none"/></svg></div>
    <time>Maret 19, 2025</time><h4>Most popular attractions 2025</h4>
    <p>Explore the top travel destinations that highlight the significance of maintaining solar panels for sustainable energy.</p>
  </article>
  <article class="post" style="left:315px">
    <div class="ph" role="img" aria-label="Boardwalk down to a rocky beach" style="background:linear-gradient(#b7d0e4,#6fa3c0 40%,#b9a083 75%)"></div>
    <div class="go"><svg width="12" height="12"><path d="M2 10L10 2M4 2h6v6" stroke="#2f6fbf" stroke-width="1.6" fill="none"/></svg></div>
    <time>Maret 19, 2025</time><h4>Tips for saving on travel</h4>
    <p>In order to understand the importance of the solar panel cleaning segment,</p>
  </article>
  <article class="post" style="left:609px">
    <div class="ph" role="img" aria-label="Tropical bay with palm trees" style="background:linear-gradient(#8fc2e3,#3a8a5c 45%,#3fb3c2 75%)"></div>
    <div class="go"><svg width="12" height="12"><path d="M2 10L10 2M4 2h6v6" stroke="#2f6fbf" stroke-width="1.6" fill="none"/></svg></div>
    <time>Feb 10, 2025</time><h4>Cultural experiences to seek out</h4>
    <p>Discover the cultural nuances of different regions and how solar energy impacts local traditions and practices.</p>
  </article>
  <article class="post" style="left:903px">
    <div class="ph" role="img" aria-label="Canal lined with old buildings and boats" style="background:linear-gradient(#9cc2df,#8a6d55 50%,#2f6e6a)"></div>
    <div class="go"><svg width="12" height="12"><path d="M2 10L10 2M4 2h6v6" stroke="#2f6fbf" stroke-width="1.6" fill="none"/></svg></div>
    <time>Maret 19, 2025</time><h4>The future of eco-friendly travel</h4>
    <p>Investigate how emerging technologies in solar energy are reshaping the travel industry and promoting eco-conscious adventures.</p>
  </article>
</section>

<!-- Contact band -->
<section>
  <div class="abs" role="img" aria-label="Turquoise ocean water texture" style="left:0;top:3026px;width:1200px;height:304px;background:linear-gradient(120deg,#58b6d6,#8fd0e4 45%,#4aa7cc)"></div>
  <div class="pill on" style="left:548px;top:3060px;width:104px;background:#e9f0fa">Contact</div>
  <h2 class="abs center" style="top:3102px;font-size:32px;font-weight:500;line-height:50px;color:#fff"><span class="accent">Ready to Embark</span> on Your<br>Next Adventure</h2>
  <div class="btn" style="left:468px;top:3239px;width:265px;height:35px">Get Started now</div>
</section>

<!-- About -->
<section>
  <p class="abs" style="left:80px;top:3427px;font-size:12px">About Us</p>
  <h2 class="abs h2" style="left:80px;top:3444px;line-height:50px">Discover your <span class="accent">dream<br>sea journey</span></h2>
  <p class="abs" style="left:80px;top:3570px;width:410px;font-size:13px;font-weight:600;line-height:22px">Join an unforgettable sea adventure with Glacierra! Enjoy the beauty of the vast ocean while exploring exotic islands and witnessing amazing marine life. From tranquil cruises to thrilling snorkeling experiences, every moment will bring you closer to the wonders of nature. Find joy in every wave and create memories that will last a lifetime!</p>
  <p class="abs lead" style="left:80px;top:3748px;width:420px;font-size:12.5px">Our vision is to inspire love for the ocean and its conservation, while our mission is to provide a safe and educational experience for every traveller.</p>
  <div class="btn" style="left:80px;top:3845px;width:136px;height:36px">Get Started now</div>

  <div class="ph" role="img" aria-label="Beach with granite boulders and palms" style="left:600px;top:3387px;width:320px;height:314px;background:linear-gradient(#4f8fd0,#a9cce6 40%,#3d6e4a 65%,#d8cbb0)"></div>
  <div class="ph" role="img" aria-label="Heron beside clay pots by the sea" style="left:940px;top:3387px;width:228px;height:158px;background:linear-gradient(#a9d0e8,#b8bcbf 55%,#a4573a)"></div>
  <div class="ph" role="img" aria-label="Waves rolling onto sand from above" style="left:807px;top:3568px;width:322px;height:312px;background:linear-gradient(110deg,#1f6f86,#7fb9c4 45%,#e8e6dd 55%,#cfc4b1)"></div>
  <svg class="abs" style="left:1070px;top:3820px" width="84" height="84"><defs><pattern id="dot" width="8" height="8" patternUnits="userSpaceOnUse"><circle cx="2" cy="2" r="1.3" fill="#2f6fbf"/></pattern></defs><rect width="84" height="84" fill="url(#dot)" opacity=".7"/></svg>
  <div class="abs" style="left:612px;top:3718px;width:178px;height:197px;background:#3a86e0;border-radius:10px;color:#fff;text-align:center;padding-top:38px">
    <div style="font-size:48px;font-weight:500;line-height:52px">120+</div>
    <div style="display:flex;justify-content:center;margin-top:14px">
      <i style="width:24px;height:24px;border-radius:50%;background:#e0b88f;border:2px solid #fff"></i><i style="width:24px;height:24px;border-radius:50%;background:#7d5a48;border:2px solid #fff;margin-left:-6px"></i><i style="width:24px;height:24px;border-radius:50%;background:#c49a7c;border:2px solid #fff;margin-left:-6px"></i><i style="width:24px;height:24px;border-radius:50%;background:#4c3c34;border:2px solid #fff;margin-left:-6px"></i><i style="width:24px;height:24px;border-radius:50%;background:#d8a888;border:2px solid #fff;margin-left:-6px"></i><i style="width:24px;height:24px;border-radius:50%;background:#6b4e3d;border:2px solid #fff;margin-left:-6px"></i>
    </div>
    <div style="display:flex;justify-content:center;align-items:center;gap:3px;margin-top:6px;font-size:12px">4.9&nbsp;<svg width="18" height="18"><use href="#star"/></svg><svg width="18" height="18"><use href="#star"/></svg><svg width="18" height="18"><use href="#star"/></svg><svg width="18" height="18"><use href="#star"/></svg><svg width="18" height="18"><use href="#star"/></svg></div>
  </div>
</section>

<!-- Testimonials -->
<section>
  <h2 class="abs center h2" style="top:3975px"><span class="accent">Customer</span> Testimonials</h2>
  <p class="abs lead" style="top:4030px;left:330px;width:540px;text-align:center">Explore our customer sub-menu! Here, you can find everything from personalized recommendations to exclusive deals. Check out our top-rated local restaurants, exciting water activities</p>

  <article class="quote" style="left:64px">
    <div class="who"><div class="av"></div><div><b>Milo Hartley</b><span>Monaco</span></div>
      <div class="stars"><svg width="20" height="20"><use href="#star"/></svg><svg width="20" height="20"><use href="#star"/></svg><svg width="20" height="20"><use href="#star"/></svg><svg width="20" height="20"><use href="#star"/></svg><svg width="20" height="20"><use href="#star"/></svg></div></div>
    <span class="qm" style="left:20px;top:92px">“</span><span class="qm" style="right:20px;top:146px">”</span>
    <p>Our ship's journey was truly amazing! The blue sea and clear sky welcomed us warmly.</p>
  </article>
  <article class="quote" style="left:437px">
    <div class="who"><div class="av"></div><div><b>Serena Voss</b><span>Italy</span></div>
      <div class="stars"><svg width="20" height="20"><use href="#star"/></svg><svg width="20" height="20"><use href="#star"/></svg><svg width="20" height="20"><use href="#star"/></svg><svg width="20" height="20"><use href="#star"/></svg><svg width="20" height="20"><use href="#star"/></svg></div></div>
    <span class="qm" style="left:20px;top:92px">“</span><span class="qm" style="right:20px;top:146px">”</span>
    <p>Our ship adventure was very impressive! The bright blue sea and shining sky greeted us with warmth.</p>
  </article>
  <article class="quote" style="left:809px">
    <div class="who"><div class="av" style="background:#2b2f35"></div><div><b>Owen Ashby</b><span>Saint Barthélemy</span></div>
      <div class="stars"><svg width="20" height="20"><use href="#star"/></svg><svg width="20" height="20"><use href="#star"/></svg><svg width="20" height="20"><use href="#star"/></svg><svg width="20" height="20"><use href="#star"/></svg><svg width="20" height="20"><use href="#star"/></svg></div></div>
    <span class="qm" style="left:20px;top:92px">“</span><span class="qm" style="right:20px;top:146px">”</span>
    <p>Our nautical expedition was unforgettable! The shimmering waves and vibrant sunsets painted a perfect backdrop.</p>
  </article>
</section>

<!-- Subscribe -->
<section>
  <div class="abs" role="img" aria-label="Dark ocean at dusk" style="left:0;top:4436px;width:1200px;height:322px;background:linear-gradient(#1c2733,#2d4356 55%,#3a5366)"></div>
  <h2 class="abs center h2" style="top:4480px;color:#fff">Subscribe <span class="accent" style="color:#4a8ee0">Now</span></h2>
  <p class="abs" style="top:4530px;left:380px;width:440px;text-align:center;font-size:12px;color:#fff;line-height:20px">Sign up now to gain exclusive access and exciting offers every month!</p>
  <div class="abs" style="left:396px;top:4602px;width:409px;height:49px;background:#fff;border-radius:25px;display:flex;align-items:center;justify-content:space-between;padding:0 8px 0 22px;font-size:12px;color:#e0a0a0">Enter Your Email
    <span style="width:60px;height:36px;border-radius:18px;background:var(--blue);display:flex;align-items:center;justify-content:center"><svg width="22" height="16" viewBox="0 0 22 16"><rect x="1" y="1" width="20" height="14" rx="2" fill="#fff"/><path d="M1 2l10 7 10-7" stroke="#2f6fbf" stroke-width="1.6" fill="none"/></svg></span></div>
</section>

<!-- Footer -->
<footer>
  <div class="abs" style="left:0;top:4758px;width:1200px;height:263px;background:var(--foot)"></div>
  <div class="abs" style="left:48px;top:4822px;display:flex;align-items:center;gap:8px;font-size:22px;font-weight:600;color:#fff"><i style="width:16px;height:16px;border-radius:50%;background:#fff;display:block"></i>Glacierra</div>
  <p class="abs" style="left:48px;top:4876px;width:405px;font-size:13px;color:#fff;line-height:21px;font-weight:300">Experience the breathtaking charm of a captivating beach destination, where the blue sky meets the gentle crashing waves. Every corner offers extraordinary natural beauty, from the soft white sands to the vibrant coral reefs.</p>
  <div class="foot-col" style="left:628px"><h5>About Us</h5>Our team<br>Mission and Values<br>Partnerships</div>
  <div class="foot-col" style="left:838px"><h5>Help</h5>FAQ<br>Booking guide<br>Sitemap</div>
  <div class="foot-col" style="left:1051px"><h5>Contact</h5>Support Team<br>Feedback<br>Live Chat</div>
  <p class="abs center" style="top:4987px;font-size:12px;color:#fff">©2025 – <b>Glacierra</b> All rights reserved.</p>
</footer>

</body>
</html>
```